Kelvaro.ch is looking for business card letterhead and envelope C5 with WOW effect

We need a strong business card for our company Kelvaro.ch, logo is available. You want a black or dark background on which the logo Stark r% 26 # 252; appears. Letterhead and envelope in C5 format should be in a similar design, but does not have to be We need a strong business card for our company Kelvaro.ch, logo is available. A black or dark background is desired, on which the logo Stark comes across. The letterhead and the envelope in C5 format should have a similar design.

Target Market(s)

Private customers as well as entrepreneurs

Contact Information for Business Card

E-mail: info@kelvaro-example.ch
Web.www.Kelvaro-example.ch
Tel: +41 ( 0 ) 79 482 6037
Adresse:
Lindenweg 14
9406 Tarnbach

Hier kann man Icons verwenden für Email,Tel und Adressse

Font styles to use
Other font styles liked:
• Dubai,bold

Colors

Designer to choose colors to be used in the design.

Requirements
Must have
• WOW effect
Nice to have
• R% 26 # 252; back business card with our service listings. - VEHICLE LABELING - SHOP WINDOW LABELING - STICKERS AND MUCH MORE ... in red color

```html
<!DOCTYPE html>
<html lang="en">
<head>
<meta charset="utf-8">
<title>Kelvaro.ch – Business Card</title>
<link rel="stylesheet" href="https://fonts.googleapis.com/css2?family=Arimo:wght@400&family=Ubuntu:wght@500;700&display=swap">
<style>
  :root {
    --backdrop: #d6d6d6;
    --brand-yellow: #fdcb1c;
    --brand-yellow-deep: #e9b920;
    --brand-black: #050505;
    --ink: #111111;
    --white: #ffffff;
  }
  * { margin: 0; padding: 0; box-sizing: border-box; }
  html, body {
    width: 1200px;
    height: 802px;
    overflow: hidden;
    background: var(--backdrop);
  }
  .canvas {
    position: relative;
    width: 1200px;
    height: 802px;
  }
  .card {
    position: absolute;
    top: 274px;
    width: 443px;
    height: 265px;
    overflow: hidden;
  }

  /* Front side */
  .card--front {
    left: 136px;
    background: var(--brand-yellow);
    color: var(--ink);
  }
  .card__pattern-area {
    position: absolute;
    top: 0;
    right: 0;
    width: 214px;
    height: 100%;
    background: linear-gradient(100deg, var(--brand-yellow) 0%, var(--brand-yellow-deep) 45%, var(--brand-yellow) 100%);
  }
  .card__name {
    position: absolute;
    left: 23px;
    top: 44px;
    font-family: "Ubuntu", sans-serif;
    font-weight: 700;
    font-size: 27px;
    letter-spacing: 0.5px;
    text-transform: uppercase;
  }
  .contact-list {
    position: absolute;
    left: 23px;
    top: 138px;
    list-style: none;
    font-family: "Arimo", sans-serif;
    font-size: 14px;
  }
  .contact-list__item {
    display: flex;
    align-items: center;
    height: 19.5px;
  }
  .contact-list__icon {
    width: 17px;
    height: 15px;
    margin-right: 7px;
    flex: none;
  }
  .card__address {
    position: absolute;
    left: 26px;
    top: 216px;
    font-family: "Arimo", sans-serif;
    font-size: 14px;
  }

  /* Back side */
  .card--back {
    left: 624px;
    background: var(--brand-black);
  }
  .brand-lockup {
    position: absolute;
    left: 100px;
    top: 100px;
    display: flex;
    align-items: center;
  }
  .brand-lockup__mark {
    width: 34px;
    height: 34px;
    background: var(--brand-yellow);
    margin-right: 20px;
  }
  .brand-lockup__name {
    font-family: "Ubuntu", sans-serif;
    font-weight: 700;
    font-size: 26px;
    letter-spacing: 0.5px;
    color: var(--white);
    text-transform: uppercase;
  }
  .services-band {
    position: absolute;
    left: 0;
    bottom: 0;
    width: 100%;
    height: 52px;
    background: var(--brand-yellow);
    display: flex;
    flex-direction: column;
    align-items: center;
    justify-content: center;
    font-family: "Ubuntu", sans-serif;
    font-weight: 500;
    font-size: 11px;
    line-height: 14px;
    color: var(--ink);
    text-transform: uppercase;
  }
</style>
</head>
<body>
<main class="canvas">

  <section class="card card--front" aria-label="Business card front">
    <div class="card__pattern-area" role="img" aria-label="Decorative honeycomb pattern in yellow tones"></div>
    <h1 class="card__name">Kelvaro.ch</h1>
    <ul class="contact-list">
      <li class="contact-list__item">
        <svg class="contact-list__icon" viewBox="0 0 17 15" aria-hidden="true">
          <rect x="1" y="0.5" width="15" height="14" rx="2" fill="none" stroke="#111" stroke-width="1.3"/>
          <path d="M5.5 3.5c.8-.5 1.6 1.5 1.2 2-.4.5-.8.5-.3 1.5.5 1 1.3 1.8 2.2 2.2.6.3 1-.4 1.4-.6.5-.2 2.3 1 1.8 1.7-.6.9-1.7 1.2-2.8.7C7 10 5.2 8 4.6 6c-.3-1.1 0-2 .9-2.5z" fill="#111"/>
        </svg>
        <span>+41 ( 0 ) 79 482 6037</span>
      </li>
      <li class="contact-list__item">
        <svg class="contact-list__icon" viewBox="0 0 17 15" aria-hidden="true">
          <rect x="0.5" y="2.5" width="16" height="10" fill="#111"/>
          <path d="M1 3l7.5 5.5L16 3" fill="none" stroke="#fdcb1c" stroke-width="1.2"/>
        </svg>
        <span>info@kelvaro-example.ch</span>
      </li>
      <li class="contact-list__item">
        <svg class="contact-list__icon" viewBox="0 0 17 15" aria-hidden="true">
          <g fill="none" stroke="#111" stroke-width="1.2">
            <circle cx="8.5" cy="7.5" r="6.7"/>
            <ellipse cx="8.5" cy="7.5" rx="3" ry="6.7"/>
            <path d="M1.8 7.5h13.4M3 4h11M3 11h11M8.5 .8v13.4"/>
          </g>
        </svg>
        <span>www.Kelvaro-example.ch</span>
      </li>
    </ul>
    <p class="card__address">Lindenweg 14,9406 Tarnbach</p>
  </section>

  <section class="card card--back" aria-label="Business card back">
    <div class="brand-lockup">
      <span class="brand-lockup__mark" aria-hidden="true"></span>
      <span class="brand-lockup__name">Kelvaro.ch</span>
    </div>
    <div class="services-band">
      <span>Vehicle labeling | Shop window labeling</span>
      <span>Stickers and much more ...</span>
    </div>
  </section>

</main>
</body>
</html>
```